Church needs a street sign design

We're a small church located in Silicon Valley, California. Our website is https://www.vgtmarlowfield.org/ and our address is 4817 Ferrow Ave, San Jose, California, 95873. You can look up our location on Google Maps to see the sign from Street View. I have uploaded an image of the street sign as well. The marquee, the top section of the sign, and the separating line between them both will be removed. We're seeking a design for a new backlit acrylic insert that will go on the front of the light box and the back of the lightbox. The acrylic sign will fill the entire external frame. In the future, we may build a decorative wood frame around the structural legs, as visualized in one of the uploaded files. The church's brand colors are: #003366 (dark blue), #ff6600 (vibrant orange), #228b22 (forest green). I have also uploaded the church's logo assets. Our primary font is Montserrat and the secondary is Poppins. You can deviate from these colors/fonts if the sign is still coherent with the rest of our branding. Our branding values are mission, truth, passion, and community (please do not put those words on the sign! They are just intended to guide the look of the design). The sign dimensions are 96" by 47.5". Keep in mind that the sign will be backlit on a busy street side. It will also be positioned next to an old-looking church building. We do NOT want a sign that looks traditional, old, or antiquated. Instead, we want a modern-looking sign that pairs well with our old building while helping it look more modern too. We would also like the web address clearly visible on the sign: vgtmarlowfield.org. If you have any questions, just let me know!

```html
<!DOCTYPE html>
<html lang="en">
<head>
<meta charset="utf-8">
<title>Valley Grace Tabernacle – Street Sign</title>
<link rel="stylesheet" href="https://fonts.googleapis.com/css2?family=Playfair+Display:wght@900&family=Poppins:wght@400;500;700&family=Montserrat:wght@600&display=swap">
<style>
  :root {
    --navy: #233561;
    --white: #ffffff;
    --orange: #e06f37;
    --orange-soft: rgba(224, 111, 55, 0.55);
    --orange-clear: rgba(224, 111, 55, 0);
  }
  html, body {
    margin: 0;
    padding: 0;
    width: 1200px;
    height: 587px;
    overflow: hidden;
    background: var(--navy);
  }
  .sign {
    position: relative;
    width: 1200px;
    height: 587px;
    background: var(--navy);
    color: var(--white);
    overflow: hidden;
  }
  .brand-art {
    position: absolute;
    left: 740px;
    top: 0;
    width: 460px;
    height: 587px;
    background:
      radial-gradient(ellipse 55% 60% at 62% 40%, var(--orange) 0%, var(--orange-soft) 45%, var(--orange-clear) 100%);
  }
  .brand {
    position: absolute;
    left: 73px;
    top: 56px;
    display: flex;
    align-items: center;
    gap: 16px;
  }
  .brand-mark {
    width: 22px;
    height: 22px;
    background: var(--white);
  }
  .brand-name {
    font-family: "Montserrat", sans-serif;
    font-weight: 600;
    color: var(--white);
    font-size: 22px;
    line-height: 1.1;
    letter-spacing: 0.04em;
    text-transform: uppercase;
    margin: 0;
  }
  .headline {
    position: absolute;
    left: 73px;
    top: 164px;
    margin: 0;
    font-family: "Playfair Display", serif;
    font-weight: 900;
    font-size: 140px;
    line-height: 128px;
    letter-spacing: -0.01em;
    color: var(--white);
  }
  .headline span { display: block; }
  .service {
    position: absolute;
    left: 73px;
    top: 462px;
    margin: 0;
    font-family: "Poppins", sans-serif;
    font-weight: 500;
    font-size: 32px;
    line-height: 38px;
    color: var(--white);
  }
  .web {
    position: absolute;
    right: 527px;
    top: 498px;
    margin: 0;
    font-family: "Poppins", sans-serif;
    font-size: 32px;
    line-height: 38px;
    color: var(--white);
    text-decoration: none;
  }
  .web-name { font-weight: 700; }
  .web-tld { font-weight: 400; }
</style>
</head>
<body>
  <main class="sign">
    <div class="brand-art" role="img" aria-label="Large orange church brand symbol decoration"></div>

    <header class="brand">
      <div class="brand-mark" aria-hidden="true"></div>
      <p class="brand-name">Valley Grace<br>Tabernacle</p>
    </header>

    <h1 class="headline">
      <span>Faith and</span>
      <span>Practice</span>
    </h1>

    <p class="service">Sunday Service<br>10:40 am</p>

    <a class="web" href="https://www.vgtmarlowfield.org/"><span class="web-name">vgtmarlowfield</span><span class="web-tld">.org</span></a>
  </main>
</body>
</html>
```